Meridale Partners Website

Meridale Partners (MP) provide Analytics & Enterprise Performance Management (EPM) advisory & consultancy services. We are passionate about data and making a difference for our clients by working in partnership with them, helping them on their journey to becoming an Meridale Partner. We deliver insights which give our clients a competitive edge and a much deeper understanding of their organisation.

We need a website which shows who we are, what we do and how we do it.

www.meridale-partners.example is our very basic website at the moment. We want to completely revamp it with a corporate look

```html
<!DOCTYPE html>
<html lang="en">
<head>
<meta charset="utf-8">
<title>Meridale Partners – Data Analytics &amp; EPM Consulting</title>
<link rel="stylesheet" href="https://fonts.googleapis.com/css2?family=Montserrat:wght@500;600;700;800&family=Arimo:wght@400;500&display=swap">
<style>
  :root {
    --navy: #2b5470;
    --navy-deep: #1f445d;
    --navy-soft: #3c6a88;
    --ink: #333a40;
    --body: #555b61;
    --footer: #1a1a1a;
    --footer-text: #d9d9d9;
    --white: #ffffff;
    --card-border: #e6e9ec;
    --accent-blue: #6fb6e6;
  }
  * { box-sizing: border-box; margin: 0; padding: 0; }
  html, body { width: 1200px; height: 3202px; overflow: hidden; }
  body {
    position: relative;
    background: var(--white);
    font-family: "Arimo", Arial, sans-serif;
    color: var(--body);
  }
  .abs { position: absolute; }
  .heading { font-family: "Montserrat", Arial, sans-serif; }

  /* Hero */
  .hero-art { position: absolute; left: 0; top: 0; width: 1200px; height: 850px; }
  .site-header { position: absolute; left: 0; top: 0; width: 1200px; height: 117px; background: rgba(43,84,112,0.92); }
  .brand {
    position: absolute; left: 112px; top: 30px;
    display: flex; align-items: center; gap: 14px;
    font-family: "Montserrat", Arial, sans-serif; font-weight: 700;
    color: var(--white); font-size: 24px; line-height: 28px; letter-spacing: 0.5px;
  }
  .brand-dot { width: 40px; height: 40px; border-radius: 50%; background: var(--white); flex: none; }
  .main-nav { position: absolute; top: 47px; left: 447px; font-family: "Montserrat", Arial, sans-serif; font-weight: 600; font-size: 15px; color: var(--white); }
  .main-nav a { position: absolute; white-space: nowrap; color: inherit; text-decoration: none; }
  .btn-started {
    position: absolute; left: 943px; top: 29px; width: 145px; height: 52px;
    border: 2px solid var(--white); border-radius: 26px;
    display: flex; align-items: center; justify-content: center;
    font-family: "Montserrat", Arial, sans-serif; font-weight: 600; font-size: 15px; color: var(--white);
  }
  .hero-copy { position: absolute; left: 0; width: 1200px; text-align: center; color: var(--white); font-family: "Montserrat", Arial, sans-serif; text-shadow: 0 3px 8px rgba(0,0,0,0.35); }
  .hero-kicker { top: 365px; font-size: 56px; font-weight: 700; letter-spacing: 1px; }
  .hero-title { top: 420px; font-size: 84px; font-weight: 800; letter-spacing: 2px; }
  .hero-sub { top: 530px; font-size: 27px; font-weight: 700; }
  .slider-dots { position: absolute; top: 782px; left: 576px; display: flex; gap: 7px; }
  .slider-dots span { width: 12px; height: 12px; border-radius: 50%; background: var(--white); }
  .slider-dots span.active { background: var(--accent-blue); }

  /* Section headings */
  .section-title { position: absolute; font-family: "Montserrat", Arial, sans-serif; font-weight: 600; font-size: 37px; }
  .rule { position: absolute; height: 3px; width: 40px; }

  /* What we do */
  .service-card {
    position: absolute; top: 1013px; width: 307px; height: 395px;
    border: 1px solid var(--card-border); border-radius: 14px; background: var(--white);
    box-shadow: 0 2px 12px rgba(0,0,0,0.08); text-align: center;
  }
  .service-card svg { position: absolute; top: 22px; left: 103px; }
  .service-card h3 { position: absolute; top: 136px; width: 100%; font-family: "Montserrat", Arial, sans-serif; font-weight: 600; font-size: 20px; color: var(--ink); }
  .service-card .card-rule { position: absolute; top: 174px; left: 134px; width: 38px; height: 2px; background: var(--navy); }
  .service-card p { position: absolute; top: 190px; left: 30px; width: 247px; font-size: 14px; line-height: 26px; color: var(--body); }
  .btn-outline {
    position: absolute; top: 311px; left: 87px; width: 134px; height: 46px;
    border: 2px solid var(--navy); border-radius: 23px;
    display: flex; align-items: center; justify-content: center;
    font-family: "Montserrat", Arial, sans-serif; font-weight: 600; font-size: 14px; color: var(--navy);
  }

  /* How we do it */
  .how-band { position: absolute; left: 0; top: 1490px; width: 1200px; height: 680px; }
  .how-item { position: absolute; left: 112px; width: 460px; color: var(--white); }
  .how-item .ring { position: absolute; left: 0; top: 0; width: 85px; height: 85px; border: 2px solid var(--white); border-radius: 50%; }
  .how-item .ring svg { position: absolute; left: 20px; top: 20px; }
  .how-item h4 { position: absolute; left: 109px; top: 7px; font-family: "Montserrat", Arial, sans-serif; font-weight: 600; font-size: 18px; white-space: nowrap; }
  .how-item p { position: absolute; left: 109px; top: 38px; width: 320px; font-size: 14px; line-height: 23px; }

  /* Who we are */
  .who-mark { position: absolute; left: 180px; top: 2330px; width: 420px; text-align: center; font-family: "Montserrat", Arial, sans-serif; font-weight: 700; font-size: 60px; line-height: 74px; color: var(--navy); }
  .who-text { position: absolute; left: 665px; top: 2337px; width: 354px; font-size: 14px; line-height: 26px; text-align: justify; color: var(--body); }
  .btn-solid {
    position: absolute; left: 663px; top: 2573px; width: 166px; height: 54px; border-radius: 27px;
    background: var(--navy); color: var(--white);
    display: flex; align-items: center; justify-content: center;
    font-family: "Montserrat", Arial, sans-serif; font-weight: 600; font-size: 16px;
  }

  /* Footer */
  .footer-band { position: absolute; left: 0; top: 2775px; width: 1200px; height: 427px; }
  .footer-brand { top: 2888px; font-size: 24px; }
  .footer-about { position: absolute; left: 112px; top: 2965px; width: 250px; font-size: 14px; line-height: 26px; color: var(--footer-text); text-align: justify; }
  .footer-heading { position: absolute; top: 2883px; font-family: "Montserrat", Arial, sans-serif; font-weight: 600; font-size: 21px; color: var(--white); }
  .footer-links { position: absolute; left: 438px; top: 2930px; list-style: none; font-size: 14px; color: var(--white); }
  .footer-links li { height: 26.5px; display: flex; align-items: center; gap: 16px; }
  .footer-links li::before { content: ""; width: 8px; height: 8px; border: 1.5px solid #6b8fa8; border-radius: 50%; }
  .contact-list { position: absolute; left: 620px; top: 2930px; font-size: 14px; line-height: 21px; color: var(--white); }
  .contact-row { position: relative; padding-left: 23px; margin-bottom: 10px; }
  .contact-row svg { position: absolute; left: 0; top: 3px; }
  .contact-label { color: #5d8fb3; }
  .newsletter-text { position: absolute; left: 866px; top: 2930px; width: 224px; font-size: 14px; line-height: 26px; color: var(--white); text-align: justify; }
  .newsletter-input { position: absolute; left: 866px; top: 2996px; width: 223px; height: 43px; border: 1px solid #cfcfcf; background: var(--footer); color: var(--white); font-size: 13px; padding-left: 14px; display: flex; align-items: center; }
  .newsletter-submit { position: absolute; left: 866px; top: 3048px; width: 112px; height: 41px; background: var(--navy); color: var(--white); font-size: 16px; display: flex; align-items: center; justify-content: center; }
  .footer-divider { position: absolute; left: 112px; top: 3120px; width: 976px; height: 1px; background: #333; }
  .copyright { position: absolute; left: 0; top: 3157px; width: 1200px; text-align: center; font-size: 16px; color: var(--white); }
</style>
</head>
<body>

  <!-- Hero -->
  <svg class="hero-art" viewBox="0 0 1200 850" role="img" aria-label="Photograph of business team silhouettes against a city skyline, blue tinted">
    <defs>
      <linearGradient id="heroPhoto" x1="0" y1="0" x2="1" y2="1">
        <stop offset="0" stop-color="#4e6f86"/>
        <stop offset="0.35" stop-color="#6f8fa5"/>
        <stop offset="0.7" stop-color="#4a6f8b"/>
        <stop offset="1" stop-color="#2d5673"/>
      </linearGradient>
      <radialGradient id="heroWarm" cx="0.05" cy="0.6" r="0.35">
        <stop offset="0" stop-color="#d7945a" stop-opacity="0.55"/>
        <stop offset="1" stop-color="#d7945a" stop-opacity="0"/>
      </radialGradient>
    </defs>
    <polygon points="0,0 1200,0 1200,740 802,849 0,745" fill="url(#heroPhoto)"/>
    <polygon points="0,0 1200,0 1200,740 802,849 0,745" fill="url(#heroWarm)"/>
    <polygon points="0,745 802,849 1200,740 1200,752 802,850 0,748" fill="var(--navy)"/>
    <polygon points="0,745 802,849 1200,740 1200,740 802,762 30,748" fill="var(--navy-deep)"/>
  </svg>

  <header class="site-header">
    <div class="brand"><span class="brand-dot"></span><span>MERIDALE<br>PARTNERS</span></div>
    <nav class="main-nav">
      <a style="left:0">HOME</a>
      <a style="left:108px">SERVICES</a>
      <a style="left:240px">ABOUT US</a>
      <a style="left:379px">CONTACT US</a>
    </nav>
    <div class="btn-started">GET STARTED</div>
  </header>

  <div class="hero-copy hero-kicker">MERIDALE</div>
  <div class="hero-copy hero-title">PARTNERS</div>
  <div class="hero-copy hero-sub">DATA ANALYTICS &amp; EPM CONSULTING SERVICES</div>
  <div class="slider-dots"><span></span><span class="active"></span><span></span></div>

  <!-- What we do -->
  <h2 class="section-title" style="left:0;width:1200px;text-align:center;top:914px;color:var(--ink)">WHAT WE DO</h2>
  <div class="rule" style="left:580px;top:972px;background:var(--navy)"></div>

  <article class="service-card" style="left:110px">
    <svg width="100" height="100" viewBox="0 0 100 100" fill="none" stroke="var(--navy)" stroke-width="3" stroke-linecap="round">
      <path d="M38 66 C38 56 28 52 28 38 a22 22 0 0 1 44 0 c0 14 -10 18 -10 28 z"/>
      <path d="M40 73 h20 M42 80 h16 M46 87 h8"/>
      <path d="M50 60 v-22 M45 38 a5 5 0 0 1 10 0"/>
      <path d="M50 4 v8 M18 16 l6 6 M82 16 l-6 6 M8 44 h8 M84 44 h8"/>
    </svg>
    <h3>ADVISE &amp; ARCHITECT</h3>
    <div class="card-rule"></div>
    <p>Working with our partners to develop comprehensive, enterprise-wide data strategy. Helping to identify any gaps in should be taken to fill them.</p>
    <div class="btn-outline">READ MORE</div>
  </article>

  <article class="service-card" style="left:445px">
    <svg width="100" height="100" viewBox="0 0 100 100" fill="none" stroke="var(--navy)" stroke-width="3" stroke-linecap="round" stroke-linejoin="round">
      <rect x="10" y="20" width="78" height="70" rx="3"/>
      <path d="M10 30 h50"/>
      <path d="M30 78 l6 -16 l40 -48 l10 9 l-40 48 z M36 62 l10 9"/>
    </svg>
    <h3>DESIGN &amp; IMPLEMENT</h3>
    <div class="card-rule"></div>
    <p>Building cost efficient "best" solutions that deliver speedy agile solutions. Solutions that are fully documented and optimised for future maintenance</p>
    <div class="btn-outline">READ MORE</div>
  </article>

  <article class="service-card" style="left:780px">
    <svg width="100" height="100" viewBox="0 0 100 100" fill="none" stroke="var(--navy)" stroke-width="3" stroke-linecap="round">
      <circle cx="50" cy="16" r="8"/>
      <path d="M38 38 a12 12 0 0 1 24 0 z"/>
      <path d="M50 38 v14 M22 52 h56 M22 52 v10 M50 52 v10 M78 52 v10"/>
      <circle cx="22" cy="72" r="9"/><circle cx="50" cy="72" r="9"/><circle cx="78" cy="72" r="9"/>
    </svg>
    <h3>OPTIMISE &amp; MANAGE</h3>
    <div class="card-rule"></div>
    <p>Working with our partners to develop comprehensive, enterprise-wide data strategy. Helping to identify any gaps in should be taken to fill them.</p>
    <div class="btn-outline">READ MORE</div>
  </article>

  <!-- How we do it -->
  <svg class="how-band" viewBox="0 1490 1200 680" preserveAspectRatio="none">
    <defs>
      <linearGradient id="howPhotoFade" x1="0" y1="0" x2="1" y2="0">
        <stop offset="0" stop-color="#2b5470" stop-opacity="1"/>
        <stop offset="0.35" stop-color="#5d86a6" stop-opacity="0.9"/>
        <stop offset="1" stop-color="#a9c4d8" stop-opacity="0.85"/>
      </linearGradient>
    </defs>
    <polygon points="0,1569 435,1492 1200,1569 1200,2099 790,2167 0,2099" fill="var(--navy)"/>
    <polygon role="img" aria-label="Photograph of hands working on a laptop with floating data charts" points="620,1500 1200,1560 1200,2099 790,2167 620,2140" fill="url(#howPhotoFade)"/>
  </svg>

  <h2 class="section-title" style="left:111px;top:1618px;color:var(--white)">HOW WE DO IT</h2>
  <div class="rule" style="left:112px;top:1675px;background:var(--white)"></div>

  <div class="how-item" style="top:1720px">
    <div class="ring"><svg width="45" height="45" viewBox="0 0 45 45" fill="none" stroke="#fff" stroke-width="2"><rect x="4" y="6" width="37" height="30"/><path d="M10 30 v-8 M17 30 v-12 M24 30 v-6 M31 30 v-14 M9 18 l8 -5 l7 4 l9 -7"/></svg></div>
    <h4>PROVIDE ANALYTICS</h4>
    <p>Sed ut perspiciatis unde omnis iste natus error sit voluptatem accusantium doloremque</p>
  </div>
  <div class="how-item" style="top:1833px">
    <div class="ring"><svg width="45" height="45" viewBox="0 0 45 45" fill="none" stroke="#fff" stroke-width="2"><circle cx="22.5" cy="18" r="7"/><path d="M22.5 4 v7 M22.5 25 v14 M8 18 h7 M30 18 h7 M12 8 l5 5 M33 8 l-5 5"/><circle cx="22.5" cy="4" r="2"/><circle cx="6" cy="18" r="2"/><circle cx="39" cy="18" r="2"/></svg></div>
    <h4>ENTERPRISE PERFORMANCE</h4>
    <p>Sed ut perspiciatis unde omnis iste natus error sit voluptatem accusantium doloremque</p>
  </div>
  <div class="how-item" style="top:1947px">
    <div class="ring"><svg width="45" height="45" viewBox="0 0 45 45" fill="none" stroke="#fff" stroke-width="2"><circle cx="13" cy="10" r="5"/><circle cx="32" cy="10" r="5"/><circle cx="22.5" cy="24" r="5"/><rect x="2" y="20" width="12" height="9" rx="2"/><rect x="31" y="20" width="12" height="9" rx="2"/><path d="M14 40 a8.5 8.5 0 0 1 17 0"/></svg></div>
    <h4>ADVISORY &amp; CONSULTANCY</h4>
    <p>Sed ut perspiciatis unde omnis iste natus error sit voluptatem accusantium doloremque</p>
  </div>

  <!-- Who we are -->
  <div class="who-mark">MERIDALE<br>PARTNERS</div>
  <h2 class="section-title" style="left:662px;top:2256px;color:var(--navy)">WHO WE ARE</h2>
  <div class="rule" style="left:666px;top:2314px;width:54px;background:var(--navy)"></div>
  <p class="who-text">MP are a Data Analytics &amp; EPM company, specialising in the implementation and support of Business Intelligence, EPM and Data Analytics business solutions, both in the Cloud and on-premise. Meridale Partners is an exciting start-up in the Data Analytics and EPM space. Founded in 2019, MP specialise in the implementation and support of BI, EPM and Data Analytics business solutions, both in the Cloud and on-premise.</p>
  <div class="btn-solid">READ MORE</div>

  <!-- Footer -->
  <svg class="footer-band" viewBox="0 2775 1200 427" preserveAspectRatio="none">
    <polygon points="0,2825 767,2781 1200,2823 1200,3202 0,3202" fill="var(--footer)"/>
  </svg>

  <div class="brand footer-brand" style="top:2888px"><span class="brand-dot"></span><span>MERIDALE<br>PARTNERS</span></div>
  <p class="footer-about">Sed ut perspiciatis unde omnis iste natus error sit voluptatem accusantium dolo remque laudantium, totam rem aperiam, quae ab illo inventore veritatis</p>

  <h3 class="footer-heading" style="left:438px">LINKS</h3>
  <ul class="footer-links">
    <li>Home</li><li>Services</li><li>About Us</li><li>Contact Us</li>
  </ul>

  <h3 class="footer-heading" style="left:620px">CONTACT</h3>
  <div class="contact-list">
    <div class="contact-row">
      <svg width="13" height="13" viewBox="0 0 24 24" fill="#5d8fb3"><path d="M6.6 10.8a15 15 0 0 0 6.6 6.6l2.2-2.2a1 1 0 0 1 1-.25 11.4 11.4 0 0 0 3.6.6 1 1 0 0 1 1 1V20a1 1 0 0 1-1 1A17 17 0 0 1 3 4a1 1 0 0 1 1-1h3.5a1 1 0 0 1 1 1c0 1.25.2 2.45.6 3.6a1 1 0 0 1-.25 1z"/></svg>
      <span class="contact-label">Phone &nbsp;&nbsp;:</span><br>+1 888 888 8888
    </div>
    <div class="contact-row">
      <svg width="14" height="12" viewBox="0 0 24 20" fill="#5d8fb3"><path d="M0 2h24v16H0z M2 4l10 7 10-7" stroke="#1a1a1a" stroke-width="2"/></svg>
      <span class="contact-label">Email &nbsp;&nbsp;&nbsp;&nbsp;:</span><br>info@company.com
    </div>
    <div class="contact-row">
      <svg width="11" height="14" viewBox="0 0 20 26" fill="#5d8fb3"><path d="M10 0a10 10 0 0 0-10 10c0 7.5 10 16 10 16s10-8.5 10-16A10 10 0 0 0 10 0zm0 14a4 4 0 1 1 0-8 4 4 0 0 1 0 8z"/></svg>
      <span class="contact-label">Address :</span><br>#154 Lorem Ispum Dummy<br>Lorem Ipsum lorem
    </div>
  </div>

  <h3 class="footer-heading" style="left:866px">NEWSLETTER</h3>
  <p class="newsletter-text">Sed ut perspiciatis unde omnis iste natus error sit voluptatem</p>
  <div class="newsletter-input">Enter Your Email</div>
  <div class="newsletter-submit">Submit</div>

  <div class="footer-divider"></div>
  <p class="copyright">©2022 Meridale Partners.All rights reserved.</p>

</body>
</html>
```